Varnik Holdings — Business Card Design Brief
Overview
Design a double-sided business card for Varnik Holdings that highlights our two service arms: Varnik Communications (telecommunications) and Varnik Energy (business energy solutions). The card should feel smart and stand out when handed to clients.

Objectives
Showcase our areas of specialty clearly.
Reflect the overall Varnik / Varnik Holdings brand while acknowledging both arms.
Explore using both logos (Communications + Energy) or one unified logo, depending on the design.

Deliverables
One double-sided business card design (front + back).

Content & Copy
Front (preferred): Logo: Varnik / Varnik Holdings
Descriptor: Business Communications | Business Energy
Back:My contact details and company details
Core products: Business Mobile • Telephony • Internet • Business Energy Solutions

Brand & Visual Direction
We have a group logo currently tailored more toward telecoms, plus a separate Varnik Energy logo.
Please explore layouts that use both logos or just one, whichever works best.
Color: I wouldn't mind seeing an option using our the Blue/Purple gradient from our website (varnik-example.co.uk), but also open to non-gradient approaches and other colours..

Overall look: Smart, modern, and distinctive.
Format & Print Specs
Double-sided business card format. (Use a standard size

Must-Haves
Front: Varnik wording or Varnik Holdings wording with atleast 1 logo also on front “Business Communications | Business Energy.”

Back: Contact + company details and core products.
A design that stands out while remaining professional.

Nice-to-Have Options
A gradient version using our site’s Blue/Purple gradient.
A non-gradient version.
A dual-logo treatment versus a single-logo treatment.

Thanks
Owen

```html
<!DOCTYPE html>
<html lang="en">
<head>
<meta charset="utf-8">
<title>Varnik Holdings — Business Card</title>
<link rel="stylesheet" href="https://fonts.googleapis.com/css2?family=Montserrat:wght@400;500;600;700&family=Oswald:wght@600&family=Libre+Baskerville&display=swap">
<style>
  :root {
    --purple: #8c16c8;
    --violet: #5a3ab4;
    --blue: #0f67a0;
    --navy: #1c1a5c;
    --energy-green: #3aa61c;
    --comms-blue: #1a6fd6;
    --ink: #1e1e2a;
    --paper: #ffffff;
    --stage: #e9e9ec;
    --brand-gradient: linear-gradient(90deg, var(--purple) 0%, var(--violet) 55%, var(--blue) 100%);
  }
  * { box-sizing: border-box; margin: 0; padding: 0; }
  html, body { width: 1200px; height: 694px; overflow: hidden; }
  body {
    background: var(--stage);
    font-family: "Montserrat", sans-serif;
    display: flex;
    align-items: center;
    justify-content: center;
    gap: 40px;
  }
  .card {
    width: 540px;
    height: 310px;
    border-radius: 22px;
    position: relative;
    overflow: hidden;
    box-shadow: 0 6px 18px rgba(0,0,0,0.12);
  }

  /* Front */
  .card--front {
    background: linear-gradient(30deg, var(--purple) 0%, var(--violet) 50%, var(--blue) 100%);
    display: flex;
    flex-direction: column;
    align-items: center;
    justify-content: center;
    gap: 22px;
  }
  .front-brands {
    display: flex;
    align-items: center;
    justify-content: center;
    gap: 26px;
  }
  .brand-tile {
    background: var(--paper);
    width: 190px;
    height: 108px;
    display: flex;
    align-items: center;
    justify-content: center;
    gap: 10px;
  }
  .front-divider {
    width: 1px;
    height: 130px;
    background: rgba(255,255,255,0.85);
  }
  .front-descriptor {
    font-family: "Montserrat", sans-serif;
    font-weight: 500;
    font-size: 14px;
    letter-spacing: 1px;
    color: var(--paper);
    white-space: nowrap;
  }
  .brand-dot {
    width: 26px;
    height: 26px;
    border-radius: 50%;
    flex: none;
  }
  .brand-dot--energy { background: var(--energy-green); }
  .brand-dot--comms { background: var(--comms-blue); }
  .brand-name {
    font-family: "Montserrat", sans-serif;
    font-weight: 700;
    color: var(--navy);
    font-size: 30px;
    letter-spacing: 0.5px;
  }

  /* Back */
  .card--back { background: var(--paper); }
  .back-brands {
    position: absolute;
    left: 26px;
    top: 62px;
    display: flex;
    flex-direction: column;
    gap: 26px;
  }
  .back-brands .brand-lockup {
    display: flex;
    align-items: center;
    gap: 8px;
  }
  .back-brands .brand-name { font-size: 26px; }
  .back-brands .brand-dot { width: 22px; height: 22px; }
  .back-divider {
    position: absolute;
    left: 212px;
    top: 40px;
    width: 1px;
    height: 170px;
    background: linear-gradient(180deg, var(--violet), rgba(90,58,180,0.1));
  }
  .contact {
    position: absolute;
    left: 236px;
    top: 34px;
    right: 20px;
  }
  .contact-name {
    font-weight: 700;
    font-size: 25px;
    background: var(--brand-gradient);
    -webkit-background-clip: text;
    background-clip: text;
    color: transparent;
    line-height: 1.1;
  }
  .contact-role {
    font-family: "Libre Baskerville", serif;
    font-size: 12px;
    color: var(--ink);
    margin: 2px 0 12px;
  }
  .contact-list { list-style: none; }
  .contact-list li {
    display: flex;
    align-items: center;
    gap: 8px;
    font-size: 12.5px;
    color: var(--ink);
    margin-bottom: 7px;
  }
  .contact-icon { width: 14px; height: 14px; flex: none; fill: var(--violet); }
  .contact-address {
    font-size: 12.5px;
    color: var(--ink);
    line-height: 1.5;
    margin: 10px 0 0 22px;
  }
  .products-band {
    position: absolute;
    left: 0; right: 0; bottom: 0;
    height: 44px;
    background: var(--brand-gradient);
    display: flex;
    align-items: center;
    justify-content: center;
    color: var(--paper);
    font-family: "Oswald", sans-serif;
    font-weight: 600;
    font-size: 17px;
    letter-spacing: 0.3px;
    white-space: nowrap;
  }
</style>
</head>
<body>
  <section class="card card--front" aria-label="Business card front">
    <div class="front-brands">
      <div class="brand-tile">
        <span class="brand-dot brand-dot--energy"></span>
        <span class="brand-name">Varnik</span>
      </div>
      <div class="front-divider"></div>
      <div class="brand-tile">
        <span class="brand-dot brand-dot--comms"></span>
        <span class="brand-name">Varnik</span>
      </div>
    </div>
    <p class="front-descriptor">Business Communications | Business Energy</p>
  </section>

  <section class="card card--back" aria-label="Business card back">
    <div class="back-brands">
      <div class="brand-lockup">
        <span class="brand-dot brand-dot--energy"></span>
        <span class="brand-name">Varnik</span>
      </div>
      <div class="brand-lockup">
        <span class="brand-dot brand-dot--comms"></span>
        <span class="brand-name">Varnik</span>
      </div>
    </div>
    <div class="back-divider"></div>
    <div class="contact">
      <p class="contact-name">Maren Holt</p>
      <p class="contact-role">Owner</p>
      <ul class="contact-list">
        <li>
          <svg class="contact-icon" viewBox="0 0 24 24" aria-hidden="true"><path d="M6.6 10.8a15.1 15.1 0 0 0 6.6 6.6l2.2-2.2a1 1 0 0 1 1-.25 11.4 11.4 0 0 0 3.6.57 1 1 0 0 1 1 1V20a1 1 0 0 1-1 1A17 17 0 0 1 3 4a1 1 0 0 1 1-1h3.5a1 1 0 0 1 1 1c0 1.25.2 2.45.57 3.6a1 1 0 0 1-.25 1z"/></svg>
          020-555 0142 7
        </li>
        <li>
          <svg class="contact-icon" viewBox="0 0 24 24" aria-hidden="true"><path d="M2 5h20v14H2z M4 7v.4l8 5.2 8-5.2V7z" fill-rule="evenodd"/></svg>
          info@varnik-example.co.uk
        </li>
        <li>
          <svg class="contact-icon" viewBox="0 0 24 24" aria-hidden="true"><path d="M12 2a10 10 0 1 0 0 20 10 10 0 0 0 0-20zm6.9 6h-3a15.6 15.6 0 0 0-1.4-3.6A8 8 0 0 1 18.9 8zM12 4a14 14 0 0 1 1.9 4h-3.8A14 14 0 0 1 12 4zM4.3 14a8 8 0 0 1 0-4h3.4a16.5 16.5 0 0 0 0 4zm.8 2h3a15.6 15.6 0 0 0 1.4 3.6A8 8 0 0 1 5.1 16zm3-8h-3a8 8 0 0 1 4.4-3.6A15.6 15.6 0 0 0 8.1 8zM12 20a14 14 0 0 1-1.9-4h3.8A14 14 0 0 1 12 20zm2.3-6H9.7a14.7 14.7 0 0 1 0-4h4.6a14.7 14.7 0 0 1 0 4zm.2 5.6a15.6 15.6 0 0 0 1.4-3.6h3a8 8 0 0 1-4.4 3.6zm1.8-5.6a16.5 16.5 0 0 0 0-4h3.4a8 8 0 0 1 0 4z"/></svg>
          www.varnik-example.co.uk
        </li>
      </ul>
      <p class="contact-address">17, Harrow Mill Lane East<br>LN4 2QT, United Kingdom</p>
    </div>
    <div class="products-band">Business Mobile • Telephony • Internet • Business Energy Solutions</div>
  </section>
</body>
</html>
```